Animal Eye Clinic needs a Business card

We are a new veterinary ophthalmology practice (Ridgeline Pet Vision Care) and we need a business card designed. We only see animal eyes - we are not a regular veterinary clinic. We already have a logo. We are looking for a professional, good looking business card to hand out to our clients. We are looking for something simple but professional and contemporary. Our logo is likely the only picture/graphic that needs to be on the card.
Updates

Contact Information for Business Card

Delia Vossman, BSc, DVM, MSc, DipACVO
Veterinary Ophthalmologist

Phone: 250.418.3927
Email: ridgelinepetvisioncare@mailbox-example.net
Website: ridgelinepetvisioncare-example.net
Address: 1874 Thornbury Rd
Kelowna, BC, V1X 4M9

Colors

Designer to choose colors to be used in the design.

Requirements
Must have
• Our logo (attached)

```html
<!DOCTYPE html>
<html lang="en">
<head>
<meta charset="utf-8">
<title>Ridgeline Pet Vision Care – Business Card</title>
<link href="https://fonts.googleapis.com/css2?family=Roboto:wght@300;400;700&display=swap" rel="stylesheet">
<style>
  :root {
    --teal: #0a97a8;
    --teal-light: #16c4d2;
    --teal-dark: #06808f;
    --grey: #6f7275;
    --grey-mid: #8a8d90;
    --paper: #ffffff;
    --backdrop: #e4e6e8;
  }
  * { margin: 0; padding: 0; box-sizing: border-box; }
  html, body {
    width: 1200px; height: 901px; overflow: hidden;
    background: var(--backdrop);
    font-family: "Roboto", Arial, sans-serif;
  }
  .canvas { position: relative; width: 1200px; height: 901px; }

  .card {
    position: absolute;
    width: 660px; height: 377px;
    box-shadow: 0 6px 18px rgba(0,0,0,.18);
    overflow: hidden;
  }

  /* Back of card */
  .card-back {
    left: 90px; top: 50px;
    background: linear-gradient(135deg, var(--teal-dark) 0%, var(--teal) 55%, var(--teal-light) 100%);
  }
  .card-back .pattern-area { position: absolute; inset: 0; }
  .card-back .brand-mark {
    position: absolute; left: 420px; top: 172px;
    display: flex; align-items: center; gap: 8px;
    color: var(--paper); font-weight: 700; font-size: 14px; letter-spacing: .5px;
  }
  .card-back .brand-mark .dot {
    width: 14px; height: 14px; border-radius: 50%; background: var(--paper);
  }

  /* Front of card */
  .card-front { left: 450px; top: 470px; background: var(--paper); }
  .front-circle {
    position: absolute; left: 395px; top: 22px;
    width: 250px; height: 250px; border-radius: 50%;
    background: var(--teal);
  }
  .brand-name {
    position: absolute; left: 40px; top: 56px;
    color: var(--teal); font-weight: 700; font-size: 30px; line-height: 1.05;
    text-transform: uppercase; letter-spacing: -.3px;
  }
  .contact {
    position: absolute; left: 40px; top: 178px;
    color: var(--grey); font-weight: 300; font-size: 15.5px; line-height: 1.25;
  }
  .person-name { color: var(--teal); font-weight: 700; font-size: 17px; }
  .credentials { color: var(--teal); font-weight: 400; font-size: 10.5px; }
  .address { margin-top: 12px; }
  .contact-list { list-style: none; margin-top: 12px; }
  .contact-list li { display: flex; align-items: center; gap: 7px; }
  .contact-list svg { width: 11px; height: 11px; fill: var(--teal); flex: none; }
  .web-domain { color: var(--teal); }
</style>
</head>
<body>
<div class="canvas">

  <section class="card card-back">
    <div class="pattern-area" role="img" aria-label="Embossed repeat of the clinic emblem across a teal field"></div>
    <div class="brand-mark"><span class="dot"></span>Ridgeline Pet Vision Care</div>
  </section>

  <section class="card card-front">
    <div class="front-circle" role="img" aria-label="Place for the clinic emblem in a teal circle"></div>

    <h1 class="brand-name">Ridgeline<br>Pet Vision Care</h1>

    <div class="contact">
      <div><span class="person-name">Delia Vossman</span><span class="credentials">, BSc, DVM, MSc, DipACVO</span></div>
      <div class="job-title">Veterinary Ophthalmologist</div>
      <div class="address">1874 Thornbury Rd<br>Kelowna, BC, V1X 4M9</div>
      <ul class="contact-list">
        <li>
          <svg viewBox="0 0 24 24" aria-hidden="true"><path d="M6.6 10.8c1.4 2.8 3.8 5.1 6.6 6.6l2.2-2.2c.3-.3.7-.4 1-.2 1.1.4 2.3.6 3.6.6.6 0 1 .4 1 1V20c0 .6-.4 1-1 1C10.6 21 3 13.4 3 4c0-.6.4-1 1-1h3.5c.6 0 1 .4 1 1 0 1.3.2 2.5.6 3.6.1.3 0 .7-.2 1l-2.3 2.2z"/></svg>
          250.418.3927
        </li>
        <li>
          <svg viewBox="0 0 24 24" aria-hidden="true"><path d="M2 5h20v14H2z M4 7v.5l8 5 8-5V7l-8 5z" fill-rule="evenodd"/></svg>
          ridgelinepetvisioncare@mailbox-example.net
        </li>
        <li>
          <svg viewBox="0 0 24 24" aria-hidden="true"><circle cx="12" cy="12" r="10"/></svg>
          <span>www.<span class="web-domain">ridgelinepetvisioncare-example.net</span></span>
        </li>
      </ul>
    </div>
  </section>

</div>
</body>
</html>
```